Business Card for Beach theme sports bar called MORVIN

I need a business card designed for our employees, front and back. This will be used by the employees of two business locations to hand out to customers. I've attached the previous business cards we used at one time for a Dantells (it is now Morvin). Looking for a fresh new card that is elegant but has character.

Target Market(s)

30-60, middle class

Contact Information for Business Card

We are a beach bar and sports bar. I am looking for an elegant business card with the front to have the MORVIN logo. Then on the back I need it to allow a space for employees to write their names and for them to write in their schedule. I have attached our old cards with our old name Dantells so you can pull everything we need on the cards. one thing is missing is we have another location at 2615 W Calder Ridge Rd with a number of 702-418-9053. Since we will use it for both locations it should allow the employee to circle or check mark the bar which they work at.

Font styles to use
Sans Serif

Requirements
Must have
• We are looking for some fresh ideas for the business card. Something that will really stick out to customers when the staff hands them out. Creativity will be looked at positively, but we still want it to look upscale and fun.

```html
<!DOCTYPE html>
<html lang="en">
<head>
<meta charset="utf-8">
<title>Morvin – Business Card</title>
<link rel="stylesheet" href="https://fonts.googleapis.com/css2?family=Montserrat:wght@400;600&family=Lobster&family=Roboto+Slab:wght@400&family=Abril+Fatface&display=swap">
<style>
  :root {
    --page: #f0f0f0;
    --card-top: #d4664d;
    --card-bottom: #cd553a;
    --sea: #6ea7b7;
    --sea-deep: #3f6f86;
    --sand: #f4e3bb;
  }
  * { margin: 0; padding: 0; box-sizing: border-box; }
  html, body { width: 1200px; height: 900px; overflow: hidden; background: var(--page); }
  .canvas { position: relative; width: 1200px; height: 900px; }

  .card {
    position: absolute;
    top: 340px;
    width: 392px;
    height: 224px;
    background: linear-gradient(160deg, var(--card-top), var(--card-bottom));
    box-shadow: 0 14px 22px rgba(0,0,0,0.18);
  }
  .card--front { left: 169px; }
  .card--back { left: 638px; }

  .brand-mark {
    position: absolute;
    width: 96px; height: 96px;
    display: flex; align-items: center; justify-content: center;
  }
  .brand-mark svg { position: absolute; inset: 0; }
  .brand-name {
    position: relative;
    font-family: 'Montserrat', sans-serif;
    font-weight: 600;
    font-size: 21px;
    color: var(--sea);
  }
  .card--front .brand-mark { left: 59px; top: 30px; }
  .card--back .brand-mark { left: 147px; top: 10px; }

  .tagline {
    position: absolute;
    left: 181px; top: 66px;
    font-family: 'Lobster', cursive;
    font-size: 17px;
    color: var(--sea);
  }

  .location {
    position: absolute;
    top: 143px;
    width: 150px;
    text-align: center;
    font-family: 'Montserrat', sans-serif;
    font-size: 9px;
    line-height: 11px;
    color: var(--sand);
  }
  .location--one { left: 56px; }
  .location--two { left: 190px; }
  .check-box {
    display: block;
    width: 14px; height: 14px;
    margin: 0 auto 9px;
    background: var(--sand);
    border-radius: 1px;
  }

  .email {
    position: absolute;
    left: 26px; top: 105px;
    font-family: 'Montserrat', sans-serif;
    font-size: 13px;
    color: var(--sea);
  }
  .name-field {
    position: absolute;
    left: 26px; top: 132px;
    width: 235px; height: 71px;
    background: var(--sand);
    border-radius: 2px;
    padding: 3px 6px;
    font-family: 'Roboto Slab', serif;
    font-size: 13px;
    color: var(--sea-deep);
  }

  .schedule {
    position: absolute;
    right: 24px; top: 17px;
    list-style: none;
  }
  .schedule li {
    display: flex;
    align-items: center;
    justify-content: flex-end;
    height: 21px;
    margin-bottom: 6.5px;
  }
  .day {
    font-family: 'Abril Fatface', serif;
    font-size: 15px;
    color: var(--sea);
    margin-right: 8px;
  }
  .day-box {
    width: 21px; height: 21px;
    background: var(--sand);
    border-radius: 2px;
  }
</style>
</head>
<body>
<main class="canvas">

  <section class="card card--front" aria-label="Card front">
    <div class="brand-mark">
      <svg viewBox="0 0 96 96" aria-hidden="true"><circle cx="48" cy="48" r="44" fill="none" stroke="#6ea7b7" stroke-width="3"/></svg>
      <span class="brand-name">Morvin</span>
    </div>
    <p class="tagline">Beach theme sports bar</p>

    <div class="location location--one">
      <span class="check-box"></span>
      3180 W Orchard Mesa Rd<br>702-564-7120
    </div>
    <div class="location location--two">
      <span class="check-box"></span>
      2615 W Calder Ridge Rd<br>702-418-9053
    </div>
  </section>

  <section class="card card--back" aria-label="Card back">
    <div class="brand-mark">
      <svg viewBox="0 0 96 96" aria-hidden="true"><circle cx="48" cy="48" r="44" fill="none" stroke="#6ea7b7" stroke-width="3"/></svg>
      <span class="brand-name">Morvin</span>
    </div>
    <p class="email">cs@morvinbar.com</p>
    <div class="name-field">Bartender:</div>

    <ul class="schedule">
      <li><span class="day">M</span><span class="day-box"></span></li>
      <li><span class="day">T</span><span class="day-box"></span></li>
      <li><span class="day">W</span><span class="day-box"></span></li>
      <li><span class="day">Th</span><span class="day-box"></span></li>
      <li><span class="day">F</span><span class="day-box"></span></li>
      <li><span class="day">Sa</span><span class="day-box"></span></li>
      <li><span class="day">Su</span><span class="day-box"></span></li>
    </ul>
  </section>

</main>
</body>
</html>
```